Locksmith Business Cards

My father-in-law is in need of new business cards for his locksmith business and I need to impress him. Kindly help me out!

You can see the previous business card attached. It is a family run business in North Wales.

No individual names on the cards.

Key Things to Feature:
- The words "Prompt", "Local", "Reliable" (as you can see under the logo on the website)
- 24h Emergency Service
- Covering All of North Wales, the Wirral and Chester
- The color blue
- A key or a lock would be interesting (similar to the ones that come up when you google locksmith business card)

Optional (only if design includes bullet points, like the example below):
https://imgvaultcdn.net/samples/208314/55172/55172_3904821_208314_image.jpg
- Residential / Commercial / Automotive
- Alarms & Cameras
- Key Cutting & Safes

https://www.brynhafod-locksmiths.co.uk/

Industry/Entity Type

Locksmith

Contact Information for Business Card

01632 960 418
07700 900 362
brynhafodlocksmiths@mailvane.com
Brynhafod Locksmiths, The Willow Barn, 7 Tannery Rd., Llandudno LL99 4QX
www.brynhafod-locksmiths.co.uk

Requirements
Must have
• - The words "Prompt", "Local", "Reliable" (as you can see under the logo on the website)
• - 24h Emergency Service
• - Covering All of North Wales, the Wirral and Chester
Nice to have
• - A key or a lock would be interesting (similar to the ones that come up when you google locksmith business card)

```html
<!DOCTYPE html>
<html lang="en">
<head>
<meta charset="utf-8">
<title>Brynhafod Locksmiths – Business Cards</title>
<link href="https://fonts.googleapis.com/css2?family=Open+Sans:wght@400;600;700&family=Roboto:wght@700&display=swap" rel="stylesheet">
<style>
  :root {
    --navy: #262a67;
    --band-blue: #4a5ea3;
    --soft-blue: #5c6cb5;
    --white: #ffffff;
    --paper: #f7f7f8;
    --stage: #1d1d1f;
  }
  * { margin: 0; padding: 0; box-sizing: border-box; }
  html, body {
    width: 1200px; height: 1021px; overflow: hidden;
    background: var(--stage);
    font-family: "Open Sans", sans-serif;
  }
  .sheet {
    position: relative; width: 1200px; height: 1021px;
  }
  .card {
    position: absolute; left: 290px; width: 620px; height: 380px;
    overflow: hidden; border-radius: 4px;
  }

  /* ---------- Back of card ---------- */
  .card-back { top: 95px; background: var(--navy); color: var(--white); }
  .card-back .brand-block {
    position: absolute; right: 40px; top: 70px; width: 360px; text-align: center;
  }
  .card-back .brand-name {
    font-weight: 700; font-size: 40px; line-height: 1.05;
    text-transform: uppercase; letter-spacing: 0.5px; color: var(--white);
  }
  .est-line {
    display: flex; align-items: center; gap: 12px; margin: 10px 0 18px;
    color: var(--soft-blue); font-size: 16px;
  }
  .est-line::before, .est-line::after {
    content: ""; flex: 1; height: 1px; background: var(--soft-blue);
  }
  .service-list { list-style: none; font-size: 17px; line-height: 1.35; }
  .card-back .web {
    margin-top: 28px; font-weight: 700; font-size: 17px; letter-spacing: 0.8px;
  }

  /* ---------- Front of card ---------- */
  .card-front { top: 530px; background: var(--paper); color: var(--navy); }
  .card-front .brand-name {
    position: absolute; left: 40px; top: 34px;
    font-weight: 700; font-size: 34px; line-height: 1.05;
    text-transform: uppercase; color: var(--navy);
  }
  .contact {
    position: absolute; left: 70px; top: 130px; list-style: none;
  }
  .contact li { display: flex; align-items: center; gap: 8px; }
  .contact .phone { font-weight: 700; font-size: 22px; line-height: 1.25; }
  .contact .email { font-size: 15px; margin-top: 4px; }
  .contact svg { width: 16px; height: 16px; flex: none; }
  .address {
    position: absolute; left: 40px; top: 222px; font-size: 15px;
  }
  .emergency-band {
    position: absolute; left: 0; top: 252px; width: 430px; height: 40px;
    background: var(--band-blue); color: var(--white);
    font-weight: 700; font-size: 21px; letter-spacing: 0.8px;
    display: flex; align-items: center; justify-content: center;
  }
  .coverage {
    position: absolute; left: 20px; top: 302px; font-size: 15px; width: 430px; text-align: center;
  }
  .values-panel {
    position: absolute; right: 0; top: 0; width: 170px; height: 380px;
    background: var(--navy); color: var(--white);
    display: flex; flex-direction: column; justify-content: flex-end;
    padding: 0 0 50px 24px;
    font-family: "Roboto", sans-serif; font-weight: 700; font-size: 24px; line-height: 1.5;
  }
</style>
</head>
<body>
<main class="sheet">

  <section class="card card-back" aria-label="Business card back">
    <div class="brand-block">
      <h1 class="brand-name">Brynhafod Locksmiths</h1>
      <p class="est-line">Est Since 1989</p>
      <ul class="service-list">
        <li>Residential / Commercial / Automotive</li>
        <li>Alarms &amp; Cameras</li>
        <li>Key Cutting &amp; Safes</li>
      </ul>
      <p class="web">www.brynhafod-locksmiths.co.uk</p>
    </div>
  </section>

  <section class="card card-front" aria-label="Business card front">
    <h2 class="brand-name">Brynhafod<br>Locksmiths</h2>
    <ul class="contact">
      <li class="phone">
        <svg viewBox="0 0 16 16" aria-hidden="true"><path fill="#262a67" d="M3.5 1.5l2.5 0 1 3.5-1.8 1.2a8 8 0 0 0 4.6 4.6L11 9l3.5 1v2.5c0 1-1 2-2 2A11 11 0 0 1 1.5 3.5c0-1 1-2 2-2z"/></svg>
        01632 960 418
      </li>
      <li class="phone">
        <svg viewBox="0 0 16 16" aria-hidden="true"><rect x="4" y="1" width="8" height="14" rx="1.5" fill="none" stroke="#262a67" stroke-width="1.4"/><circle cx="8" cy="12.5" r="0.9" fill="#262a67"/></svg>
        07700 900 362
      </li>
      <li class="email">
        <svg viewBox="0 0 16 16" aria-hidden="true"><rect x="1.5" y="3.5" width="13" height="9" fill="none" stroke="#262a67" stroke-width="1.3"/><path d="M1.5 3.5l6.5 5 6.5-5" fill="none" stroke="#262a67" stroke-width="1.3"/></svg>
        brynhafodlocksmiths@mailvane.com
      </li>
    </ul>
    <p class="address">The Willow Barn, 7 Tannery Rd., Llandudno LL99 4QX</p>
    <p class="emergency-band">24H EMERGENCY SERVICE</p>
    <p class="coverage">Covering All of North Wales, the Wirral and Chester</p>
    <div class="values-panel">
      <span>Prompt.</span>
      <span>Local.</span>
      <span>Reliable</span>
    </div>
  </section>

</main>
</body>
</html>
```